Pre-workout label and Super Greens label for Brightmoor Nutrition Supplements

I need a label design for Club Brightmoor's 2 supplements. The first is a Pre-workout. The Pre-workout label needs to be 11.25 x 2.5 inches. This label will go on a black container. The second is a Super-Green. The Super-Green label should be 11.25 x 4.25 inches and will go on a white container. We have been selling these for a few years but the current labels are a little meh. I'd like something trendier and bolder. Must keep the Club Brightmoor branding. All the nurtition data must appear . I attached the current designs so you can know the flavors, nutrtional data etc. Thank you!
Updates

I can upload the Club Brightmoor logo! If anyone can tell me how to do that.

```html
<!DOCTYPE html>
<html lang="en">
<head>
<meta charset="utf-8">
<title>Brightmoor Supplement Labels</title>
<link rel="stylesheet" href="https://fonts.googleapis.com/css2?family=Michroma&family=Russo+One&display=swap">
<style>
  :root {
    --bg: #dde9ee;
    --label-black: #0e0e0f;
    --ink-white: #f4f4f4;
    --brand-red: #e0262b;
    --deep-red: #a81d22;
    --ink-dark: #1a1a1a;
  }
  * { margin: 0; padding: 0; box-sizing: border-box; }
  html, body { width: 1200px; height: 900px; overflow: hidden; }
  body { background: var(--bg); position: relative; }

  .label { position: absolute; overflow: hidden; }
  .label--greens { left: 185px; top: 233px; width: 360px; height: 426px; }
  .label--preworkout { left: 648px; top: 320px; width: 342px; height: 358px; }
  .label__art { position: absolute; inset: 0; }

  .brand-name {
    position: absolute; transform: translateX(-50%);
    font-family: "Michroma", sans-serif; font-weight: 400;
    font-size: 14px; letter-spacing: 1px; color: var(--ink-white);
    white-space: nowrap;
  }
  .product-title {
    position: absolute; transform: translateX(-50%);
    font-family: "Russo One", sans-serif; font-size: 31px; white-space: nowrap;
    background: linear-gradient(90deg, #8a8a8a, #f5f5f5 30%, #9a9a9a 55%, #ffffff 80%, #a0a0a0);
    -webkit-background-clip: text; background-clip: text; color: transparent;
  }
  .flavor {
    position: absolute; transform: translateX(-50%);
    font-family: "Michroma", sans-serif; font-size: 12px; letter-spacing: 0.6px;
    color: var(--ink-white); white-space: nowrap;
  }
  .supplement-note {
    position: absolute; font-family: "Michroma", sans-serif; font-size: 7.5px;
    letter-spacing: 0.4px; white-space: nowrap;
  }
  .servings { position: absolute; display: flex; align-items: center; gap: 3px; }
  .servings__count { font-family: "Russo One", sans-serif; font-size: 17px; letter-spacing: 1px; }
  .servings__detail { font-family: "Michroma", sans-serif; font-size: 5px; line-height: 1.25; }

  .label--greens .supplement-note, .label--greens .servings { color: var(--ink-dark); }
  .label--preworkout .supplement-note, .label--preworkout .servings { color: var(--ink-white); }

  .benefit {
    position: absolute; transform: translateX(-50%);
    display: flex; flex-direction: column; align-items: center; gap: 3px;
    font-family: "Michroma", sans-serif; font-size: 4px; line-height: 1.3;
    text-align: center; white-space: nowrap; text-transform: uppercase;
  }
  .label--greens .benefit { color: var(--ink-dark); }
  .label--preworkout .benefit { color: var(--ink-white); }
  .benefit small { font-size: 3.6px; text-transform: none; opacity: 0.85; }
</style>
</head>
<body>

<section class="label label--greens" aria-label="Super Greens label">
  <svg class="label__art" width="360" height="426" viewBox="0 0 360 426">
    <defs>
      <linearGradient id="silver-band" x1="0" y1="0" x2="0" y2="1">
        <stop offset="0" stop-color="#f4f4f4"/>
        <stop offset="0.5" stop-color="#bfbfbf"/>
        <stop offset="1" stop-color="#8a8a8a"/>
      </linearGradient>
      <linearGradient id="silver-strip" x1="0" y1="0" x2="1" y2="0">
        <stop offset="0" stop-color="#9a9a9a"/>
        <stop offset="0.45" stop-color="#f2f2f2"/>
        <stop offset="1" stop-color="#a6a6a6"/>
      </linearGradient>
    </defs>
    <rect width="360" height="426" fill="var(--label-black)"/>
    <rect x="0" y="24" width="360" height="6" fill="url(#silver-band)"/>
    <polygon points="0,318 270,318 290,348 360,348 360,380 0,380" fill="url(#silver-band)"/>
    <rect x="290" y="0" width="50" height="334" fill="var(--label-black)"/>
    <rect x="295" y="0" width="40" height="330" fill="url(#silver-strip)"/>
    <g fill="none" stroke="var(--brand-red)" stroke-width="1.2">
      <circle cx="315" cy="116" r="9"/>
      <circle cx="315" cy="111" r="2"/>
      <path d="M312 115 h6 v7 h-6 z"/>
      <path d="M313 186 v6 h5 a3 3 0 0 1 0 6 h-6 a3 3 0 0 0 0 6 h6"/>
      <path d="M315 262 l9 3 v6 c0 6 -4 9 -9 11 c-5 -2 -9 -5 -9 -11 v-6 z"/>
    </g>
  </svg>

  <div class="brand-name" style="left:140px; top:150px;">Brightmoor</div>
  <div class="product-title" style="left:147px; top:208px;">Super Greens</div>
  <div class="flavor" style="left:140px; top:264px;">APPLE CINNAMON</div>

  <div class="benefit" style="left:315px; top:130px;">Detox<br>Body*</div>
  <div class="benefit" style="left:315px; top:212px;">Promote<br>Healthy<br>Digestion*</div>
  <div class="benefit" style="left:315px; top:292px;">Support<br>Immunity*</div>

  <div class="supplement-note" style="left:53px; top:329px;">DIETARY SUPPLEMENT</div>
  <div class="servings" style="left:73px; top:342px;">
    <span class="servings__count">30</span>
    <span class="servings__detail">SERVINGS<br>270g (9.5oz)</span>
  </div>
</section>

<section class="label label--preworkout" aria-label="Pre-Workout label">
  <svg class="label__art" width="342" height="358" viewBox="0 0 342 358">
    <rect width="342" height="358" fill="var(--label-black)"/>
    <rect x="0" y="19" width="342" height="7" fill="var(--brand-red)"/>
    <polygon points="0,287 258,287 278,320 342,320 342,348 0,348" fill="var(--brand-red)"/>
    <rect x="275" y="0" width="52" height="310" fill="var(--label-black)"/>
    <rect x="280" y="0" width="42" height="306" fill="var(--deep-red)"/>
    <g fill="none" stroke="var(--ink-white)" stroke-width="1.2">
      <path d="M303 94 l-6 10 h5 l-3 9 l8 -12 h-5 l3 -7 z"/>
      <path d="M294 180 v-4 M298 180 v-7 M302 180 v-10 M306 180 v-13 M292 181 h18"/>
      <path d="M294 168 l14 -13 M304 155 h4 v4"/>
      <path d="M294 254 c0 -7 3 -10 6 -13 l4 -3 c2 -1 4 1 3 3 l-3 3 c3 2 6 5 6 9 c0 3 -3 5 -7 5 h-9 z"/>
    </g>
  </svg>

  <div class="brand-name" style="left:130px; top:132px;">Brightmoor</div>
  <div class="product-title" style="left:127px; top:192px;">Pre-Workout</div>
  <div class="flavor" style="left:130px; top:248px;">WATERMELON SUGAR</div>

  <div class="benefit" style="left:301px; top:121px;">Energy*<small>(Caffeine)</small></div>
  <div class="benefit" style="left:301px; top:192px;">Performance*<small>(Beta-alanine)</small></div>
  <div class="benefit" style="left:301px; top:266px;">Strength*<small>(Creatine)</small></div>

  <div class="supplement-note" style="left:50px; top:306px;">DIETARY SUPPLEMENT</div>
  <div class="servings" style="left:69px; top:318px;">
    <span class="servings__count">30</span>
    <span class="servings__detail">SERVINGS<br>240g (8.5oz)</span>
  </div>
</section>

</body>
</html>
```